Workshop PPT Update for AI Transformation Sessions

Our strategic consulting firm runs strategy workshops using slides as workshop exercises. These slides are used to communicate to the participants in advance, run the workshops and produce the final deliverable.

It is time for a design "upgrade". We'd like them to be more engaging, hipper and more interesting. These slides are utilitarian, so clean and usable is good. I have attached the example of what we have today. I have also attached an example of another company's slides that I like.

We can't rip off their design nor can we go away 100% from what we have. But I think it is possible to "update" our look to something closer to their look. Grey colors are fine with some color pop.

Slide styles needed are - 1) Cover Page, 2) Instructions Page, 3) Bullet list 4) Worksheet (place for participants to add content 5) Table, 6) Two column.

```html
<!DOCTYPE html>
<html lang="en">
<head>
<meta charset="utf-8">
<title>ClearPath – Kickoff &amp; Discovery Workshop Slides</title>
<link rel="stylesheet" href="https://fonts.googleapis.com/css2?family=Oswald:wght@400;500;600&family=Poppins:ital,wght@0,400;0,500;0,600;0,700;0,800;1,400&display=swap">
<style>
:root{
  --red:#b84a40;
  --navy:#1e2738;
  --ink:#222222;
  --muted:#555555;
  --panel:#f2f2f2;
  --row:#eeeeee;
  --black:#202020;
  --white:#ffffff;
}
*{box-sizing:border-box;margin:0;padding:0}
html,body{width:1200px;height:3652px;overflow:hidden;background:var(--white)}
body{position:relative;font-family:"Poppins",sans-serif;color:var(--ink)}
.slide{position:absolute;left:99px;width:997px;height:562px;background:var(--panel);overflow:hidden}
.abs{position:absolute}
.heading{font-family:"Oswald",sans-serif;font-weight:500;color:var(--navy);letter-spacing:.5px;line-height:1}
.rule{position:absolute;height:4px;width:78px;background:var(--red)}
.footer{position:absolute;left:0;bottom:0;width:997px;height:48px}
.footer-brand{position:absolute;left:12px;bottom:10px;color:var(--white);font-weight:500;font-size:22px;letter-spacing:-.3px}
.page-no{position:absolute;right:16px;bottom:11px;width:26px;height:26px;border-radius:50%;background:var(--black);color:var(--white);font-size:12px;font-weight:600;display:flex;align-items:center;justify-content:center}
.photo{position:absolute;left:0;top:0;width:498px;height:514px}
.photo-title{position:absolute;left:86px;font-family:"Oswald",sans-serif;font-weight:500;color:var(--white);font-size:50px;line-height:1.02;letter-spacing:.5px}
.photo-line{position:absolute;left:86px;width:78px;height:4px;background:var(--white)}
.check-icon{position:absolute;width:26px;height:26px}
.step{position:absolute;left:524px;display:flex;align-items:flex-start}
.step-num{width:40px;height:40px;border-radius:50%;background:var(--red);color:var(--white);font-weight:600;font-size:15px;display:flex;align-items:center;justify-content:center;flex:none;margin-right:16px}
.step-title{font-weight:700;font-size:19px;color:var(--black);line-height:1.2}
.step-note{font-size:10.5px;color:var(--muted);line-height:1.4;margin-top:3px;max-width:380px}
.card-shadow{position:absolute;background:var(--black)}
.card{position:absolute;background:var(--white);box-shadow:0 2px 6px rgba(0,0,0,.12)}
.card-label{color:var(--red);font-weight:600;font-size:18px}
.card-list{list-style:none}
.card-list li{font-size:16px;display:flex;align-items:center;height:31px}
.card-list li svg{width:16px;height:16px;margin-right:8px}
.task-text{position:absolute;left:556px;font-size:18px;color:var(--black)}
.principle{position:absolute;left:556px}
.principle h3{font-weight:700;font-size:20px;color:var(--black);line-height:1.2}
.principle p{font-size:10.5px;color:var(--muted);line-height:1.6}
.plan-table{position:absolute;left:28px;top:118px;width:942px;border-collapse:collapse;border:2px solid var(--black);font-size:10.5px;color:var(--muted)}
.plan-table th{background:var(--navy);color:var(--white);font-weight:500;font-size:12px;text-align:left;height:38px;padding-left:22px;letter-spacing:.3px}
.plan-table td{padding-left:22px;border-right:1px solid #dddddd}
.plan-table tr:nth-child(even) td{background:var(--row)}
.plan-table tr:nth-child(odd) td{background:var(--white)}
.plan-table .sub{padding-left:12px}
.hl{color:var(--red)}
</style>
</head>
<body>

<svg width="0" height="0" style="position:absolute" aria-hidden="true">
  <symbol id="tick-badge" viewBox="0 0 26 26">
    <circle cx="13" cy="13" r="13" fill="#b84a40"/>
    <circle cx="13" cy="13" r="7.5" fill="none" stroke="#fff" stroke-width="1.4"/>
    <path d="M9.6 13.2l2.3 2.3 4.3-4.6" fill="none" stroke="#fff" stroke-width="1.6" stroke-linecap="round" stroke-linejoin="round"/>
  </symbol>
  <symbol id="tick" viewBox="0 0 16 16">
    <path d="M2.5 8.5l3.5 3.5 7.5-8" fill="none" stroke="#b84a40" stroke-width="2.4" stroke-linecap="round" stroke-linejoin="round"/>
  </symbol>
  <symbol id="footer-band" viewBox="0 0 997 48">
    <polygon points="0,0 862,0 881,48 0,48" fill="#b84a40"/>
  </symbol>
</svg>

<!-- Cover -->
<section class="slide cover" style="top:56px;background:linear-gradient(180deg,#5f93a6 0%,#8fb6c2 45%,#6f9aa8 75%,#4f7f90 100%)">
  <div class="abs" role="img" aria-label="Digital figure dissolving into particles above a reflective futuristic landscape" style="inset:0;background:radial-gradient(ellipse at 78% 40%,rgba(220,236,242,.75) 0%,rgba(150,190,205,.3) 30%,rgba(90,140,160,0) 60%)"></div>
  <div class="abs" style="left:16px;top:140px;font-size:64px;font-weight:500;color:#2f3a44;letter-spacing:-1px">ClearPath</div>
  <div class="abs" style="left:14px;top:235px;font-size:60px;font-weight:800;color:var(--white);line-height:.92">Kickoff<br>&amp; Discovery</div>
  <div class="abs" style="left:16px;top:375px;font-size:28px;font-weight:600;color:var(--white)">Sizing &amp; Scoping AI Transformation</div>
</section>

<!-- Getting Started -->
<section class="slide" style="top:645px">
  <div class="photo" role="img" aria-label="Two colleagues reviewing documents together in an office" style="background:linear-gradient(160deg,#6b6f73 0%,#3c4450 45%,#1f2836 100%)"></div>
  <div class="photo-line" style="top:251px;left:83px"></div>
  <div class="photo-title" style="top:264px;left:83px">GETTING STARTED</div>
  <svg class="check-icon" style="left:508px;top:142px"><use href="#tick-badge"/></svg>
  <div class="task-text" style="top:141px">Complete the Engagement Sizing Survey.</div>
  <svg class="check-icon" style="left:508px;top:225px"><use href="#tick-badge"/></svg>
  <div class="task-text" style="top:224px">Collect relevant inputs.</div>
  <svg class="check-icon" style="left:508px;top:308px"><use href="#tick-badge"/></svg>
  <div class="task-text" style="top:307px">Determine workshop participants &amp; date.</div>
  <svg class="check-icon" style="left:508px;top:392px"><use href="#tick-badge"/></svg>
  <div class="task-text" style="top:391px">Send invites, to include pre-work.</div>
  <svg class="footer"><use href="#footer-band"/></svg>
  <div class="footer-brand">ClearPath</div>
  <div class="page-no">2</div>
</section>

<!-- Workshop Overview -->
<section class="slide" style="top:1238px">
  <svg class="abs" style="left:17px;top:47px" width="360" height="382"><polygon points="0,0 360,0 352,11 14,11 14,382 0,382" fill="#202020"/></svg>
  <div class="card" style="left:31px;top:58px;width:468px;height:391px"></div>
  <div class="rule" style="left:58px;top:90px"></div>
  <div class="heading abs" style="left:58px;top:108px;font-size:48px">WORKSHOP OVERVIEW</div>
  <div class="abs" style="left:58px;top:175px;font-size:18px"><span class="card-label">Participants:</span> Execs</div>
  <div class="abs" style="left:58px;top:206px;font-size:18px"><span class="card-label">Duration:</span>&nbsp; 2 hrs.</div>
  <div class="abs card-label" style="left:58px;top:255px">Prep Work</div>
  <ul class="card-list abs" style="left:58px;top:284px">
    <li><svg><use href="#tick"/></svg>Org Strategy</li>
    <li><svg><use href="#tick"/></svg>2023 Goal Performance</li>
    <li><svg><use href="#tick"/></svg>Existing policies</li>
    <li><svg><use href="#tick"/></svg>Pre-thinking questions</li>
  </ul>
  <div class="abs" style="left:524px;top:46px;font-family:'Oswald',sans-serif;font-weight:500;font-size:26px;color:var(--red)">WORKSHOP FLOW</div>
  <div class="step" style="top:94px"><div class="step-num">1</div><div><div class="step-title">Confirm Company Direction</div><div class="step-note">Recap organizational purpose, values, vision &amp; winning strategy.</div></div></div>
  <div class="step" style="top:153px"><div class="step-num">2</div><div><div class="step-title" style="padding-top:3px">Develop AI Vision</div></div></div>
  <div class="step" style="top:210px"><div class="step-num">3</div><div><div class="step-title">Develop AI Guiding Principles</div><div class="step-note">Developed AI Guiding Principles, supporting policies to include<br>approved tools</div></div></div>
  <div class="step" style="top:282px"><div class="step-num">4</div><div><div class="step-title">Agree on a Governance Approach</div><div class="step-note">Agreed upon governance approach, structure, &amp; executive champion.</div></div></div>
  <div class="step" style="top:347px"><div class="step-num">5</div><div><div class="step-title">Agree on a Training &amp; Learning Approach</div><div class="step-note">Set approach to training &amp; continuous learning.</div></div></div>
  <div class="step" style="top:412px"><div class="step-num">6</div><div><div class="step-title">Determine Rollout &amp; Communication</div><div class="step-note">Organizational rollout &amp; continuous communication.</div></div></div>
  <svg class="footer"><use href="#footer-band"/></svg>
  <div class="footer-brand">ClearPath</div>
  <div class="page-no">3</div>
</section>

<!-- AI Guiding Principles -->
<section class="slide" style="top:1830px">
  <div class="photo" role="img" aria-label="Hand holding a smartphone with a glowing chatbot assistant interface" style="background:radial-gradient(ellipse at 70% 40%,#1f3a5c 0%,#142236 45%,#0c1420 100%)"></div>
  <div class="photo-line" style="top:171px;left:88px"></div>
  <div class="photo-title" style="top:185px;left:88px">AI GUIDING<br>PRINCIPLES</div>
  <div class="abs" style="left:88px;top:302px;font-size:17px;font-style:italic;color:var(--white);line-height:1.35">What guides our decision-making<br>and approach?</div>
  <svg class="check-icon" style="left:508px;top:47px"><use href="#tick-badge"/></svg>
  <div class="principle" style="top:46px"><h3>Principle #1</h3><p>Complete perspective from Executives, Directors, Managers &amp; Staff.<br>Conduct competitive analysis and customer research (optional).</p></div>
  <svg class="check-icon" style="left:508px;top:131px"><use href="#tick-badge"/></svg>
  <div class="principle" style="top:130px"><h3>Principle #2</h3><p>Complete perspective from Executives, Directors, Managers &amp; Staff.<br>Conduct competitive analysis and customer research (optional).</p></div>
  <svg class="check-icon" style="left:508px;top:221px"><use href="#tick-badge"/></svg>
  <div class="principle" style="top:220px"><h3>Principle #3</h3><p>Complete perspective from Executives, Directors, Managers &amp; Staff.<br>Conduct competitive analysis and customer research (optional).</p></div>
  <svg class="check-icon" style="left:508px;top:314px"><use href="#tick-badge"/></svg>
  <div class="principle" style="top:313px"><h3>Principle #4</h3><p>Complete perspective from Executives, Directors, Managers &amp; Staff.<br>Conduct competitive analysis and customer research (optional).</p></div>
  <svg class="check-icon" style="left:508px;top:406px"><use href="#tick-badge"/></svg>
  <div class="principle" style="top:405px"><h3>Principle #5</h3><p>Complete perspective from Executives, Directors, Managers &amp; Staff.<br>Conduct competitive analysis and customer research (optional).</p></div>
  <svg class="footer"><use href="#footer-band"/></svg>
  <div class="footer-brand">ClearPath</div>
  <div class="page-no">4</div>
</section>

<!-- Plan Structure -->
<section class="slide" style="top:2427px">
  <div class="rule" style="left:460px;top:26px"></div>
  <div class="heading abs" style="left:0;width:997px;text-align:center;top:42px;font-size:50px">PLAN STRUCTURE</div>
  <table class="plan-table">
    <colgroup><col style="width:60px"><col style="width:117px"><col style="width:267px"><col style="width:229px"><col></colgroup>
    <thead><tr><th colspan="2" style="padding-left:52px">LEVEL</th><th>PLANNING ELEMENT &amp; DEFINITION</th><th>ACCOUNTABILITY/OWNER</th><th>FREQUENCY OF MODIFICATION</th></tr></thead>
    <tbody>
      <tr style="height:70px"><td>1</td><td class="sub">What (overall)</td><td>Strategic Priorities</td><td>N/A</td><td>3+ years</td></tr>
      <tr style="height:85px"><td>1.1</td><td class="sub">What (this year)</td><td>Goals <span class="hl">(Outcomes &amp; Strategies)</span></td><td>Executive Leadership</td><td>1-3 years</td></tr>
      <tr style="height:70px"><td>1.1.1</td><td class="sub">How</td><td>Key Performance Indicators<br>and/or Initiatives</td><td></td><td>1 year (w/ qrtly targets)</td></tr>
      <tr style="height:85px"><td>1.1.1.1</td><td class="sub"></td><td>Action Items</td><td></td><td>Quarterly/Monthly</td></tr>
    </tbody>
  </table>
  <svg class="footer"><use href="#footer-band"/></svg>
  <div class="footer-brand">ClearPath</div>
  <div class="page-no">5</div>
</section>

<!-- Creating Your AI Guiding Principles -->
<section class="slide" style="top:3022px">
  <div class="rule" style="left:460px;top:31px"></div>
  <div class="heading abs" style="left:0;width:997px;text-align:center;top:47px;font-size:50px">CREATING YOUR AI GUIDING PRINCIPLES</div>
  <svg class="abs" style="left:14px;top:123px" width="362" height="345"><polygon points="0,0 362,0 354,11 14,11 14,345 0,345" fill="#202020"/></svg>
  <div class="card" style="left:28px;top:134px;width:468px;height:346px"></div>
  <div class="abs card-label" style="left:44px;top:157px">Your Existing Material</div>
  <ul class="card-list abs" style="left:44px;top:187px">
    <li><svg><use href="#tick"/></svg>Company Values</li>
    <li><svg><use href="#tick"/></svg>Current Policies (GDPR, CCPA, etc.)</li>
    <li><svg><use href="#tick"/></svg>Legal Guidance</li>
    <li><svg><use href="#tick"/></svg>OTHER</li>
  </ul>
  <div class="abs card-label" style="left:44px;top:327px">Examples for Inspiration</div>
  <div class="abs" style="left:44px;top:357px;font-size:16px">See next slides</div>
  <div class="abs card-label" style="left:44px;top:398px">PromptPal Prompts</div>
  <div class="abs" style="left:44px;top:428px;font-size:16px">Here</div>
  <div class="abs" style="left:522px;top:117px;font-size:10.5px;line-height:1.9;width:420px"><span style="font-weight:700;font-size:19px;color:var(--black)">Purpose:</span> To create behavioral statements that everyone is expected<br><span style="padding-left:94px">to adhere to.</span></div>
  <div class="abs" style="left:524px;top:168px;font-family:'Oswald',sans-serif;font-weight:500;font-size:26px;color:var(--red)">INSTRUCTIONS:</div>
  <div class="step" style="top:206px"><div class="step-num">1</div><div><div class="step-title">Create the Outline</div><div class="step-note">Determine the topics that need a principle.</div></div></div>
  <div class="step" style="top:261px"><div class="step-num">2</div><div><div class="step-title">Audit the Outline</div><div class="step-note">Look at the current policies to determine if all topics are covered</div></div></div>
  <div class="step" style="top:313px"><div class="step-num">3</div><div><div class="step-title" style="padding-top:6px">Draft the Guiding Principles</div></div></div>
  <div class="step" style="top:365px"><div class="step-num">4</div><div><div class="step-title" style="padding-top:6px">Determine which GPs need detailed</div></div></div>
  <div class="step" style="top:415px"><div class="step-num">5</div><div><div class="step-title" style="padding-top:6px">Determine which AI Tools support the GPs.</div></div></div>
  <div class="step" style="top:464px"><div class="step-num">5</div><div><div class="step-title" style="padding-top:6px">Finalize via a legal and executive review.</div></div></div>
  <svg class="footer"><use href="#footer-band"/></svg>
  <div class="footer-brand">ClearPath</div>
  <div class="page-no">6</div>
</section>

</body>
</html>
```